New business card for a regional office of a US M&A company

We need business card for a finance company, office based in Hong Kong , our Head office is in US, our business is to Merge and acquires companies , the new office will be a regional office for the Asia Pacific region. We want to use the head office logo as attached ( but don't have to be exactly the same, can be a variation to it) as a base and then add Asia Pacific alongside the logo.
We would prefer to have be bilingual Eng + Chinese, although we don't really have Chinese company name .

Industry/Entity Type

Business

Contact Information for Business Card

Clara Jo Tsang
 

VP,
APAC M&A Operations
Orin Vantage Asia Pacific Limited
 
Unit 1407, K18
18 Tai Lok Shan Road, 
Hong Kong 
 
M: +852 6038 1742
T : +852 2836 4100
F : +852 2836 4177
VOIP: 4158
 
cjtsang@orinvantage.com

Font styles to use
Serif
Sans Serif

Colors

Designer to choose colors to be used in the design.

Requirements
Must have
• APAC Office

```html
<!DOCTYPE html>
<html lang="en">
<head>
<meta charset="utf-8">
<title>Orin Vantage – Business Card</title>
<link rel="stylesheet" href="https://fonts.googleapis.com/css2?family=Open+Sans:wght@400;600;700&display=swap">
<style>
  :root {
    --page-bg: #e9e6e1;
    --card-bg: #f4f5f4;
    --ink-dark: #2e3a45;
    --ink-mid: #5a6169;
    --brand-teal: #1d8f8c;
    --brand-navy: #1f3340;
    --band-light: #ffffff;
  }
  * { box-sizing: border-box; margin: 0; padding: 0; }
  html, body {
    width: 1200px;
    height: 1047px;
    overflow: hidden;
    background: var(--page-bg);
    font-family: "Open Sans", sans-serif;
  }
  .card {
    position: absolute;
    left: 100px;
    top: 243px;
    width: 1000px;
    height: 560px;
    background: var(--card-bg);
    border-radius: 24px;
    overflow: hidden;
    box-shadow: 0 6px 24px rgba(0,0,0,0.12);
  }
  .holder-name {
    position: absolute;
    left: 80px;
    top: 100px;
    font-size: 31px;
    font-weight: 600;
    letter-spacing: 0.5px;
    color: var(--ink-dark);
    text-transform: uppercase;
  }
  .holder-title {
    position: absolute;
    left: 80px;
    top: 148px;
    font-size: 21px;
    color: var(--ink-mid);
  }
  .contact-list {
    position: absolute;
    left: 80px;
    top: 238px;
    list-style: none;
  }
  .contact-list li {
    display: flex;
    align-items: center;
    height: 27px;
    font-size: 20px;
    letter-spacing: 0.5px;
    color: var(--ink-mid);
  }
  .contact-icon {
    width: 14px;
    height: 14px;
    margin-right: 20px;
    fill: var(--brand-teal);
    flex: none;
  }
  .office-address {
    position: absolute;
    left: 80px;
    top: 380px;
    font-size: 22px;
    line-height: 31px;
    font-style: normal;
    color: var(--ink-mid);
  }
  .brand-mark {
    position: absolute;
    left: 683px;
    top: 165px;
    width: 130px;
    height: 130px;
    background: var(--brand-navy);
  }
  .brand-name {
    position: absolute;
    right: 56px;
    top: 388px;
    font-size: 48px;
    font-weight: 700;
    letter-spacing: 2px;
    color: var(--brand-teal);
    white-space: nowrap;
  }
  .card-band {
    position: absolute;
    left: 0;
    bottom: 0;
    width: 1000px;
    height: 60px;
  }
  .voip {
    position: absolute;
    left: 672px;
    bottom: 10px;
    font-size: 21px;
    letter-spacing: 0.5px;
    color: var(--band-light);
  }
</style>
</head>
<body>
  <article class="card">
    <h1 class="holder-name">Clara Jo Tsang</h1>
    <p class="holder-title">VP, APAC M&amp;A Operations</p>

    <ul class="contact-list">
      <li>
        <svg class="contact-icon" viewBox="0 0 14 14" aria-hidden="true"><rect x="3.5" y="0.5" width="7" height="13" rx="1.2"/><rect x="4.8" y="2" width="4.4" height="8" fill="var(--card-bg)"/></svg>
        +852 6038 1742
      </li>
      <li>
        <svg class="contact-icon" viewBox="0 0 14 14" aria-hidden="true"><path d="M2.5 1 L5 1 L6 4 L4.5 5.3 C5.4 7.2 6.8 8.6 8.7 9.5 L10 8 L13 9 L13 11.5 C13 12.4 12.3 13 11.4 13 C5.8 12.6 1.4 8.2 1 2.6 C1 1.7 1.6 1 2.5 1 Z"/></svg>
        +852 2836 4100
      </li>
      <li>
        <svg class="contact-icon" viewBox="0 0 14 14" aria-hidden="true"><rect x="3.5" y="1" width="7" height="4"/><rect x="1" y="5.5" width="12" height="5.5" rx="1"/><rect x="3.5" y="9.5" width="7" height="3.5"/></svg>
        +852 2836 4177
      </li>
      <li>
        <svg class="contact-icon" viewBox="0 0 14 14" aria-hidden="true"><rect x="1" y="3" width="12" height="8.5" rx="1"/><path d="M1.5 3.6 L7 7.8 L12.5 3.6" fill="none" stroke="var(--card-bg)" stroke-width="1.2"/></svg>
        cjtsang@orinvantage.com
      </li>
    </ul>

    <address class="office-address">
      Unit 1407, K18 18 Tai Lok<br>
      Shan Road, Hong Kong
    </address>

    <div class="brand-mark" aria-hidden="true"></div>
    <p class="brand-name">ORIN VANTAGE</p>

    <svg class="card-band" viewBox="0 0 1000 60" preserveAspectRatio="none" aria-hidden="true">
      <rect x="0" y="14" width="580" height="6" fill="var(--ink-dark)"/>
      <rect x="0" y="22" width="570" height="3" fill="var(--brand-teal)"/>
      <path d="M0 52 L560 52 C600 52 605 16 650 12 L1000 8 L1000 60 L0 60 Z" fill="var(--brand-teal)"/>
    </svg>
    <p class="voip">VOIP: 4158</p>
  </article>
</body>
</html>
```